New and Fresh Website Design for a Curcumin Supplement

We need to Renew the Design of our Curcumin Supplement Website.
Our Bottle Design changed (Image Attached), so we need a new website.

Our current website is this https://vantorelabs.com.br/vantore-curcumin/

We need something like this ''watercolor bush'' vibe (Image Attached)

Final Design must be Modern, Fresh, Organic.

Comunicate Safety, Wellness

IMPORTANT: Website in elementor

Target Market(s)

+50 year old

Industry/Entity Type

Supplement

Number of Pages Required

1 page

Font styles to use
Sans Serif

Requirements
Must have
• First Fold must Be Awesome. (uploaded a image example with the text it must have)

must Have all this columns
https://vantorelabs.com.br/vantore-curcumin

```html
<!DOCTYPE html>
<html lang="en">
<head>
<meta charset="utf-8">
<title>Vantore Curcumin – Vantore Labs</title>
<link rel="stylesheet" href="https://fonts.googleapis.com/css2?family=Roboto:wght@400;500;700;900&family=Raleway:wght@400;500;600;700&display=swap">
<style>
:root{
  --red:#e8401c;
  --red-dark:#d23612;
  --orange:#f7931e;
  --ink:#111;
  --text:#555;
  --muted:#777;
  --grey-bg:#eceeee;
  --footer:#0c0c0c;
  --white:#fff;
}
*{margin:0;padding:0;box-sizing:border-box}
html,body{width:1200px;height:4515px;overflow:hidden}
body{position:relative;background:var(--white);font-family:"Raleway",sans-serif;color:var(--text)}
.abs{position:absolute}
h1,h2,h3{font-family:"Roboto",sans-serif;font-weight:700;color:var(--ink);text-transform:uppercase;line-height:1.05}
.btn{position:absolute;display:flex;align-items:center;justify-content:center;gap:10px;background:var(--red);color:#fff;font-family:"Roboto",sans-serif;font-weight:700;font-size:14px;text-transform:uppercase;border-radius:3px;height:46px}
.btn svg{width:16px;height:16px}
.ph{position:absolute}

/* header */
.site-header{position:absolute;left:0;top:0;width:1200px;height:105px;border-top:5px solid var(--red);background:#fff}
.brand{position:absolute;font-family:"Roboto",sans-serif;font-weight:700;color:var(--ink);line-height:.95}
.site-header .brand{left:112px;top:30px;font-size:24px}
.nav{position:absolute;left:337px;top:40px;display:flex;gap:44px;font-family:"Roboto",sans-serif;font-size:15px;color:#333}
.nav .active{color:var(--red);border-bottom:2px solid var(--red);padding-bottom:4px}
.nav-icons{position:absolute;left:882px;top:42px;display:flex;gap:26px}
.login{position:absolute;left:978px;top:33px;width:110px;height:38px;border-radius:19px;background:var(--red);color:#fff;font-family:"Roboto",sans-serif;font-weight:700;font-size:14px;display:flex;align-items:center;justify-content:center;gap:8px}

/* hero */
.hero{position:absolute;left:0;top:105px;width:1200px;height:599px;background:linear-gradient(100deg,#fff 0%,#fff 40%,#fde3c9 55%,#f9b45a 72%,#f07a3a 88%,#f3a33a 100%)}
.hero h1{position:absolute;left:108px;top:172px;font-size:60px;font-weight:900;line-height:.95}
.hero p{position:absolute;left:110px;top:300px;width:400px;font-size:14px;line-height:25px;color:#222}
.hero .btn{left:110px;top:373px;width:163px}
.arrow-circle{position:absolute;width:32px;height:32px;border-radius:50%;background:var(--red);display:flex;align-items:center;justify-content:center}

/* benefits */
.benefits h2{position:absolute;left:594px;top:788px;font-size:38px}
.benefit-list{position:absolute;left:594px;top:908px;width:500px;list-style:none}
.benefit-list li{position:relative;padding-left:28px;font-size:13.5px;line-height:21px;color:var(--muted);margin-bottom:16px}
.benefit-list li svg{position:absolute;left:0;top:15px;width:14px;height:14px}

/* problem */
.problem{position:absolute;left:0;top:1349px;width:1200px;height:473px;background:var(--grey-bg)}
.problem h2{position:absolute;left:123px;top:60px;font-size:38px}
.underline{position:absolute;height:4px;width:66px;background:var(--red)}
.problem .lead{position:absolute;left:123px;top:175px;width:420px;font-size:14px;line-height:20px;font-weight:700;color:#111}
.problem .body{position:absolute;left:123px;top:235px;width:480px;font-size:14px;line-height:25px;color:#333}

/* joints */
.joints h2{position:absolute;left:110px;top:1901px;font-size:38px}
.joints p{position:absolute;left:583px;top:1983px;width:470px;font-size:13.5px;line-height:24.5px;color:var(--muted)}

/* testimonials */
.testimonials{position:absolute;left:0;top:2623px;width:1200px;height:531px;background:linear-gradient(180deg,#e34a24,#e23d1b 60%,#e0451f)}
.testimonials h2{position:absolute;left:0;width:1200px;top:57px;text-align:center;color:#fff;font-size:38px}
.t-card{position:absolute;background:#fff;text-align:center;padding:0 22px}
.avatar{position:absolute;width:80px;height:80px;border-radius:50%;border:4px solid #fff;background:linear-gradient(135deg,#9a7a66,#5b4638)}
.stars{font-size:18px;letter-spacing:6px;color:#111}
.t-name{color:var(--red);font-weight:600;font-size:14px;margin:8px 0 10px}
.t-quote{font-size:13.5px;line-height:21px;color:var(--muted)}

/* offers */
.offers h2{position:absolute;left:0;width:1200px;top:3230px;text-align:center;font-size:38px}
.offers .sub{position:absolute;left:0;width:1200px;top:3312px;text-align:center;font-size:14px;color:#222;text-transform:uppercase}
.o-card{position:absolute;top:3367px;width:218px;height:309px;border:1px solid #e6e6e6;box-shadow:0 2px 6px rgba(0,0,0,.06);text-align:center}
.o-card .shot{position:absolute;left:44px;top:18px;width:130px;height:150px;border-radius:6px;background:linear-gradient(160deg,#f4f4f4,#f8cfa0 55%,#e8632b)}
.o-card .price{position:absolute;left:0;width:100%;top:190px;font-size:15px}
.o-card .price s{color:#333;margin-right:10px}
.o-card .price span{color:var(--red)}
.o-card .maker{position:absolute;left:0;width:100%;top:222px;font-size:15px;color:var(--muted)}
.o-card .join{position:absolute;left:50px;top:256px;width:118px;height:34px;border:2px solid var(--red);border-radius:3px;color:var(--red);font-weight:700;font-size:14px;display:flex;align-items:center;justify-content:center}

/* trust */
.trust{position:absolute;left:0;top:3763px;width:1200px;height:375px;background:linear-gradient(180deg,#e8451f,#e23d1b)}
.trust h2{position:absolute;left:0;width:1200px;top:64px;text-align:center;color:#fff;font-size:38px}
.trust-item{position:absolute;top:195px;width:260px;text-align:center;color:#fff;font-size:14px;line-height:22px}
.trust-item svg{display:block;margin:0 auto 20px;height:74px}

/* footer */
.site-footer{position:absolute;left:0;top:4138px;width:1200px;height:377px;background:var(--footer);color:#ddd}
.site-footer .brand{left:112px;top:46px;color:#fff;font-size:30px}
.f-note{position:absolute;left:112px;top:126px;width:300px;font-size:12.5px;line-height:23px;color:#ddd}
.pay{position:absolute;top:258px;display:flex;gap:9px;left:112px}
.pay span{display:block;width:30px;height:20px;border-radius:3px;background:#f1f1f1}
.f-col{position:absolute;top:48px}
.f-col h4{color:var(--red);font-family:"Roboto",sans-serif;font-size:15px;font-weight:500;margin-bottom:18px}
.f-col li{list-style:none;font-size:14px;color:#eee;margin-bottom:14px}
.contact-row{display:flex;gap:14px;align-items:flex-start;font-size:14px;color:#eee;margin-bottom:22px;line-height:21px}
.contact-row i{flex:none;width:30px;height:30px;border-radius:50%;background:var(--red);display:flex;align-items:center;justify-content:center}
.f-rule{position:absolute;left:110px;top:307px;width:980px;height:1px;background:#333}
.copy{position:absolute;left:0;width:1200px;top:333px;text-align:center;font-size:14px;color:#eee}
</style>
</head>
<body>

<header class="site-header">
  <div class="brand">Vantore<br><span style="font-weight:400">labs</span></div>
  <nav class="nav">
    <span class="active">Home</span><span>About Us</span><span>Products</span><span>Testimonials</span><span>Contact Us</span>
  </nav>
  <div class="nav-icons">
    <svg width="16" height="16" viewBox="0 0 16 16"><circle cx="6.5" cy="6.5" r="5" fill="none" stroke="#111" stroke-width="2"/><path d="M10.5 10.5 15 15" stroke="#111" stroke-width="2.4"/></svg>
    <svg width="18" height="16" viewBox="0 0 18 16"><path d="M0 1h3l2.5 9h9L17 3H5" fill="none" stroke="#111" stroke-width="2"/><circle cx="7" cy="14" r="1.6" fill="#111"/><circle cx="14" cy="14" r="1.6" fill="#111"/></svg>
  </div>
  <div class="login">LOGIN <svg width="14" height="14" viewBox="0 0 14 14"><path d="M1 7h8M6 3.5 9.5 7 6 10.5M10 1h3v12h-3" fill="none" stroke="#fff" stroke-width="2"/></svg></div>
</header>

<section class="hero">
  <h1>Vantore<br>Nutrition</h1>
  <p>To get the full benefits of curcumin, however, it must be combined with the right supporting assets.</p>
  <div class="btn">Get Started <svg viewBox="0 0 16 16"><circle cx="8" cy="8" r="8" fill="#fff"/><path d="M6.5 4.5 10 8l-3.5 3.5" fill="none" stroke="#e8401c" stroke-width="2"/></svg></div>
  <div class="ph" role="img" aria-label="Two Vantore Curcumin supplement bottles with turmeric root artwork on a watercolor splash" style="left:683px;top:70px;width:333px;height:455px;border-radius:30px;background:linear-gradient(180deg,#e6e6e6 0%,#fafafa 20%,#f5f5f5 55%,#e9772c 80%,#d85a1f 100%)"></div>
  <div class="arrow-circle" style="left:47px;top:282px"><svg width="12" height="12" viewBox="0 0 12 12"><path d="M8 2 4 6l4 4" fill="none" stroke="#fff" stroke-width="2.4"/></svg></div>
  <div class="arrow-circle" style="left:1119px;top:282px;background:#ef5a21"><svg width="12" height="12" viewBox="0 0 12 12"><path d="M4 2l4 4-4 4" fill="none" stroke="#fff" stroke-width="2.4"/></svg></div>
</section>

<section class="benefits">
  <div class="ph" role="img" aria-label="Bowl of turmeric powder with basil leaves and a stone mortar with black pepper on an orange watercolor splash" style="left:70px;top:762px;width:473px;height:499px;border-radius:45%;background:radial-gradient(circle at 50% 45%,#d9892b 0%,#f3a24a 30%,#f7c48f 55%,rgba(255,255,255,0) 72%)"></div>
  <h2>The Benefits of the<br>Vantore Curcumin!</h2>
  <ul class="benefit-list">
    <li><svg viewBox="0 0 14 14"><path d="M1 7l4 4 8-9" fill="none" stroke="#e8401c" stroke-width="2.4"/></svg>Contains Veraplex™ Exclusive Formula up to 3x more potent that achieves results unmatched by any other supplement on the market.</li>
    <li><svg viewBox="0 0 14 14"><path d="M1 7l4 4 8-9" fill="none" stroke="#e8401c" stroke-width="2.4"/></svg>Helps Joint Health: Because it &nbsp;is rich in antioxidants, Vantore Curcumin fights free radicals, which are a major cause of pain and discomfort.</li>
    <li><svg viewBox="0 0 14 14"><path d="M1 7l4 4 8-9" fill="none" stroke="#e8401c" stroke-width="2.4"/></svg>Fights the Aging Signs of Skin and Hair, through its antioxidant properties of its formula.</li>
    <li><svg viewBox="0 0 14 14"><path d="M1 7l4 4 8-9" fill="none" stroke="#e8401c" stroke-width="2.4"/></svg>It contributes to a Strong Immune System, as turmeric helps regulate inflammatory processes and helps several antibodies in our metabolism.</li>
  </ul>
  <div class="btn" style="left:594px;top:1191px;width:163px">Learn More <svg viewBox="0 0 16 16"><circle cx="8" cy="8" r="8" fill="#fff"/><path d="M6.5 4.5 10 8l-3.5 3.5" fill="none" stroke="#e8401c" stroke-width="2"/></svg></div>
</section>

<section class="problem">
  <div class="ph" role="img" aria-label="Vantore Curcumin bottle beside a wooden bowl of turmeric powder and fresh turmeric roots" style="left:718px;top:0;width:482px;height:473px;background:linear-gradient(90deg,#eceeee 0%,#e8e2dc 35%,#e6a76a 65%,#d86a1f 100%)"></div>
  <h2>We Have<br>Solved This Problem</h2>
  <div class="underline" style="left:123px;top:149px"></div>
  <p class="lead">We've discovered a unique holistic system to make turmeric more bioavailable than ever.</p>
  <p class="body">As turmeric is not fully absorbed by your metabolism, complementing it with other clinically tested actives such as Black Cumin Seed and Zingiber officinale makes it incredibly bioavailable so that the body has access to all its benefits.</p>
  <div class="btn" style="left:123px;top:359px;width:163px">Learn More <svg viewBox="0 0 16 16"><circle cx="8" cy="8" r="8" fill="#fff"/><path d="M6.5 4.5 10 8l-3.5 3.5" fill="none" stroke="#e8401c" stroke-width="2"/></svg></div>
</section>

<section class="joints">
  <h2>The #1 Choice to Keep<br>Your Joints Healthy</h2>
  <div class="ph" role="img" aria-label="Senior doctor in a white coat with arms crossed, with a watercolor paint splash" style="left:110px;top:2041px;width:468px;height:517px;background:linear-gradient(180deg,#ededed 0%,#eaeaea 70%,#f8c07a 85%,rgba(255,255,255,0) 100%)"></div>
  <p>International research and examinations were responsible for the creation of Vantore Curcumin, which combines natural ingredients with proven efficacy, in the concentration you need to act at the root of the problem and significantly improve pain and discomfort . Vantore Curcumin lessens your pain, keeps your joints healthy, and prevents further complications. If it does not contain Veraplex™, it is not Vantore Curcumin.</p>
  <div class="btn" style="left:583px;top:2185px;width:163px">Learn More <svg viewBox="0 0 16 16"><circle cx="8" cy="8" r="8" fill="#fff"/><path d="M6.5 4.5 10 8l-3.5 3.5" fill="none" stroke="#e8401c" stroke-width="2"/></svg></div>
  <div class="ph" role="img" aria-label="Bowls of turmeric powder with fresh turmeric roots and basil leaves on a dark table" style="left:583px;top:2260px;width:419px;height:275px;background:linear-gradient(160deg,#3a2a1e 0%,#c7731f 40%,#e8951f 60%,#6b3a1a 100%)"></div>
</section>

<section class="testimonials">
  <h2>Client Testimonials</h2>
  <div class="underline" style="left:567px;top:113px"></div>
  <div class="t-card" style="left:114px;top:212px;width:277px;height:226px;padding-top:56px">
    <div class="stars">★★★★★</div>
    <div class="t-name">Rafael Duarte, 39 years old</div>
    <div class="t-quote">"Since I started taking Vantore Curcumin, I haven't felt any pain in my lower back. I recommend it to everyone."</div>
  </div>
  <div class="avatar" role="img" aria-label="Portrait of Rafael Duarte" style="left:213px;top:172px"></div>
  <div class="t-card" style="left:429px;top:189px;width:342px;height:275px;padding-top:64px">
    <div class="stars">★★★★★</div>
    <div class="t-name" style="font-size:15px">Otávio Lemos, 64 years old</div>
    <div class="t-quote">"I have taken Vantore Curcumin for 3 years, since I retired from the bus driver profession! Being able to carry my little grandson without feeling pain is what I most wanted!!!"</div>
  </div>
  <div class="avatar" role="img" aria-label="Portrait of Otávio Lemos" style="left:555px;top:147px;width:90px;height:90px"></div>
  <div class="t-card" style="left:806px;top:212px;width:280px;height:226px;padding-top:56px">
    <div class="stars">★★★★★</div>
    <div class="t-name">Helena Prado Souza, 43 years old</div>
    <div class="t-quote">"I take Vantore Curcumin for my post-workout recovery, and I can say that it's much easier to play sports without the usual pains!"</div>
  </div>
  <div class="avatar" role="img" aria-label="Portrait of Helena Prado Souza" style="left:906px;top:172px"></div>
</section>

<section class="offers">
  <h2>Enjoy the Offers!</h2>
  <div class="underline" style="left:567px;top:3284px"></div>
  <div class="sub">Exclusive factory prices for a short time!</div>
  <div class="o-card" style="left:221px"><div class="shot" role="img" aria-label="Vantore Curcumin bottle"></div><div class="price"><s>$ 801,00</s><span>$ 67,00</span></div><div class="maker">Vantore Labs</div><div class="join">Join Now</div></div>
  <div class="o-card" style="left:491px"><div class="shot" role="img" aria-label="Vantore Curcumin bottle"></div><div class="price"><s>$ 801,00</s><span>$ 67,00</span></div><div class="maker">Vantore Labs</div><div class="join">Join Now</div></div>
  <div class="o-card" style="left:760px"><div class="shot" role="img" aria-label="Vantore Curcumin bottle"></div><div class="price"><s>$ 801,00</s><span>$ 67,00</span></div><div class="maker">Vantore Labs</div><div class="join">Join Now</div></div>
</section>

<section class="trust">
  <h2>In Doubt How Much<br>Buy on the Internet?</h2>
  <div class="trust-item" style="left:98px">
    <svg viewBox="0 0 60 74" width="60"><rect x="6" y="8" width="48" height="62" rx="4" fill="none" stroke="#fff" stroke-width="5"/><rect x="20" y="2" width="20" height="12" rx="3" fill="#fff"/><path d="M16 30h28M16 42h28M16 54h20" stroke="#fff" stroke-width="5"/></svg>
    Fully Protected Personal Data</div>
  <div class="trust-item" style="left:369px">
    <svg viewBox="0 0 80 74" width="80"><path d="M4 14h22l6 8h32v44H4z" fill="#fff"/><circle cx="58" cy="54" r="17" fill="#fff" stroke="#e23d1b" stroke-width="4"/><text x="58" y="62" text-anchor="middle" font-family="Roboto,sans-serif" font-weight="700" font-size="22" fill="#e23d1b">$</text></svg>
    Financial Data Without Sharing</div>
  <div class="trust-item" style="left:620px">
    <svg viewBox="0 0 110 74" width="104"><rect x="14" y="10" width="56" height="42" fill="#fff"/><path d="M72 22h20l14 16v14H72z" fill="#fff"/><circle cx="32" cy="58" r="9" fill="#fff" stroke="#e23d1b" stroke-width="4"/><circle cx="88" cy="58" r="9" fill="#fff" stroke="#e23d1b" stroke-width="4"/><path d="M0 22h12M4 32h10M0 42h12" stroke="#fff" stroke-width="4"/></svg>
    Guaranteed Delivery on<br>Time and Return Policy</div>
  <div class="trust-item" style="left:855px">
    <svg viewBox="0 0 60 74" width="60"><path d="M30 2 56 12v24c0 18-12 30-26 36C16 66 4 54 4 36V12z" fill="#fff"/><path d="M18 38l9 9 16-18" fill="none" stroke="#e23d1b" stroke-width="6"/></svg>
    100% Reliable Shop Safely</div>
</section>

<footer class="site-footer">
  <div class="brand">Vantore<br><span style="font-weight:400">labs</span></div>
  <p class="f-note">Results may vary according to each person's metabolism The information contained on this website or in the emails sent has been prepared for educational purposes only.</p>
  <div class="pay"><span></span><span></span><span></span><span></span><span></span><span></span><span></span></div>
  <div class="f-col" style="left:489px"><h4>Quicklinks</h4><ul><li>Home</li><li>About Us</li><li>Products</li><li>Testimonials</li><li>Contact Us</li></ul></div>
  <div class="f-col" style="left:667px"><h4>Qtherlinks</h4><ul><li>Blog</li><li>Privacy</li><li>Services</li><li>Team</li></ul></div>
  <div class="f-col" style="left:836px;width:270px"><h4>Contact Us</h4>
    <div class="contact-row"><i><svg width="14" height="14" viewBox="0 0 14 14"><path d="M3 1l3 3-2 2c1 2 2 3 4 4l2-2 3 3-2 2C6 13 1 8 1 3z" fill="#fff"/></svg></i><span style="padding-top:4px">123 (555) 014</span></div>
    <div class="contact-row"><i><svg width="14" height="12" viewBox="0 0 14 12"><rect x="1" y="1" width="12" height="10" fill="none" stroke="#fff" stroke-width="1.6"/><path d="M1 1l6 5 6-5" fill="none" stroke="#fff" stroke-width="1.6"/></svg></i><span style="padding-top:4px">info@vantorelabs.com</span></div>
    <div class="contact-row"><i><svg width="12" height="14" viewBox="0 0 12 14"><path d="M6 0a5 5 0 0 1 5 5c0 4-5 9-5 9S1 9 1 5a5 5 0 0 1 5-5z" fill="#fff"/><circle cx="6" cy="5" r="2" fill="#e8401c"/></svg></i><span>122 Lorem ipsum dolor sit<br>consectetur adipiscing</span></div>
  </div>
  <div class="f-rule"></div>
  <div class="copy">©Copyrights 2021 &nbsp;Vantore Labs &nbsp; | &nbsp; All Rights Reserved &nbsp; |</div>
</footer>

</body>
</html>
```